TERRAWISPA

We are a group of friends with a passion for ancestral knowledge of potions and medicinal formulas derived from nature. We specialise in medicinal mushrooms and adaptogens. We designed a few supplement formulas which we want to release to the market. Our team comes from biology and nutritional science background. Every product we launch will be clean in biodegradable packaging.
Our first product is a lab-tested grass-fed bovine collagen type I, II, and III mixed with organic lab-tested the most potent and bioavailable medicinal mushrooms on the market. This product will be in a pouch the print will be on the pouch or on a label, we don't know if it's possible to design a label that could be used on both? We don't know if we will be able to use organic labels yet due to the legislation changes in the UK. We are waiting for clarification.
The company is called Hollow Brook. We want to use forgotten ancestral knowledge of those potions and reintroduce them to the people. We would like our brand to look clean and friendly. A natural mix of modern and ancestral design.
Our logo and brand designs we like are attached. I have attached the source file of our logo if anyone thinks colours could be different we are open to ideas. I have also attached the visual design we were playing with on canva.com.

```html
<!DOCTYPE html>
<html lang="en">
<head>
<meta charset="utf-8">
<title>TERRAWISPA – Collagen Peptides & Medicinal Mushrooms</title>
<link rel="stylesheet" href="https://fonts.googleapis.com/css2?family=Oswald:wght@300;400;700&family=Montserrat:wght@600&family=Special+Elite&display=swap">
<style>
  :root {
    --backdrop: #e4e4e4;
    --kraft: #f2c896;
    --kraft-deep: #e9b377;
    --orange: #e98a2a;
    --rust: #c8652a;
    --ink: #2e2e2e;
    --ink-soft: #3d3d3d;
    --paper: #fbfbfa;
    --teal-line: #b9d8d6;
    --leaf: #6f9a3e;
    --splash: #eda35c;
  }
  * { margin: 0; padding: 0; box-sizing: border-box; }
  html, body { width: 1200px; height: 1199px; overflow: hidden; }
  body { background: var(--backdrop); position: relative; }

  .pouch {
    position: absolute; left: 180px; top: 40px;
    width: 840px; height: 1120px;
    background: linear-gradient(180deg, var(--kraft) 0%, #f4cd9f 60%, var(--kraft) 100%);
    overflow: hidden;
  }
  .splash-band {
    position: absolute; left: 0; top: 0; width: 840px; height: 130px;
    background: linear-gradient(90deg, rgba(233,150,70,.55), rgba(240,180,110,.25) 40%, rgba(233,150,70,.5) 80%, rgba(245,190,120,.3));
  }
  .leaves-left, .leaves-right {
    position: absolute; bottom: 0; height: 200px;
    background: linear-gradient(0deg, rgba(111,154,62,.55), rgba(111,154,62,0));
  }
  .leaves-left { left: 0; width: 140px; }
  .leaves-right { right: 0; width: 160px; }

  .brand {
    position: absolute; left: 95px; top: 180px; width: 300px;
    display: flex; align-items: center; gap: 14px;
  }
  .brand-dot { width: 44px; height: 44px; border-radius: 50%; background: var(--orange); flex: none; }
  .brand-name {
    font-family: "Montserrat", sans-serif; font-weight: 600;
    font-size: 42px; line-height: 1.05; color: var(--orange);
  }

  .seal { position: absolute; left: 572px; top: 132px; width: 174px; height: 174px; }

  .tagline {
    position: absolute; left: 480px; top: 312px; width: 340px;
    font-family: "Special Elite", monospace; font-size: 23px; line-height: 34px;
    color: var(--rust); text-align: center; letter-spacing: .5px;
  }

  .paper {
    position: absolute; left: 76px; top: 407px; width: 764px; height: 532px;
    background: repeating-linear-gradient(180deg, var(--paper) 0 3px, #f1f1ef 3px 4px);
  }
  .paper-margin {
    position: absolute; left: 0; top: 0; width: 28px; height: 100%;
    background: radial-gradient(circle at 14px 14px, var(--kraft) 7px, transparent 8px) 0 0 / 28px 32px repeat-y;
  }
  .mushroom-art {
    position: absolute; left: 70px; top: 300px; width: 694px; height: 232px;
    background: linear-gradient(180deg, rgba(185,216,214,.15), rgba(185,216,214,.55));
  }

  .product-name {
    position: absolute; left: 0; top: 80px; width: 764px; text-align: center; padding-left: 60px;
    font-family: "Oswald", sans-serif; font-weight: 700; font-size: 124px; line-height: 1;
    letter-spacing: 1px;
  }
  .product-name .dark { color: var(--ink); }
  .product-name .bright { color: var(--orange); }

  .descriptor {
    position: absolute; left: 0; top: 200px; width: 764px; padding-left: 60px; text-align: center;
    font-family: "Oswald", sans-serif; font-weight: 400; font-size: 37px; color: var(--ink);
    transform: scaleX(.86); transform-origin: 430px 0;
  }
  .variant {
    position: absolute; left: 0; top: 266px; width: 764px; padding-left: 60px; text-align: center;
    font-family: "Special Elite", monospace; font-size: 29px; color: var(--orange);
  }

  .claims {
    position: absolute; left: 150px; top: 358px; display: flex; gap: 30px;
  }
  .claim { width: 126px; display: flex; flex-direction: column; align-items: center; }
  .claim svg { width: 74px; height: 74px; }
  .claim span {
    margin-top: 14px; font-family: "Oswald", sans-serif; font-weight: 300;
    font-size: 24px; color: var(--ink); white-space: nowrap;
  }

  .supplement {
    position: absolute; left: 0; top: 972px; width: 840px; text-align: center;
    font-family: "Special Elite", monospace; font-size: 34px; color: var(--rust);
  }
  .net-weight {
    position: absolute; left: 0; top: 1030px; width: 840px; text-align: center;
    font-family: "Special Elite", monospace; font-size: 30px; color: var(--ink);
  }
</style>
</head>
<body>
  <main class="pouch">
    <div class="splash-band" role="img" aria-label="Watercolour splashes in orange and green with faint leaves"></div>
    <div class="leaves-left" role="img" aria-label="Watercolour grass leaves"></div>
    <div class="leaves-right" role="img" aria-label="Watercolour grass leaves"></div>

    <div class="brand">
      <span class="brand-dot"></span>
      <span class="brand-name">Hollow Brook</span>
    </div>

    <svg class="seal" viewBox="0 0 174 174" role="img" aria-label="Lab-tested quality seal">
      <circle cx="87" cy="87" r="84" fill="none" stroke="var(--ink-soft)" stroke-width="3"/>
      <circle cx="87" cy="87" r="48" fill="none" stroke="var(--ink-soft)" stroke-width="2"/>
    </svg>

    <p class="tagline">EVERYTHING YOUR BODY NEEDS TO REPLENISH</p>

    <section class="paper">
      <div class="paper-margin"></div>
      <div class="mushroom-art" role="img" aria-label="Line illustration of ornamented mushrooms in pale teal"></div>

      <h1 class="product-name"><span class="dark">TERRA</span><span class="bright">WISPA</span></h1>
      <p class="descriptor">COLLAGEN PEPTIDES &amp; MEDICINAL MUSHROOMS</p>
      <p class="variant">TYPE I, II, III ◆ UNFLAVOURED</p>

      <ul class="claims" style="list-style:none">
        <li class="claim">
          <svg viewBox="0 0 74 74">
            <circle cx="37" cy="37" r="34" fill="#fff" stroke="var(--ink-soft)" stroke-width="2"/>
            <rect x="22" y="28" width="16" height="16" fill="none" stroke="var(--rust)" stroke-width="3"/>
            <rect x="36" y="26" width="16" height="16" fill="none" stroke="var(--rust)" stroke-width="3"/>
            <line x1="16" y1="16" x2="58" y2="58" stroke="var(--ink-soft)" stroke-width="2"/>
          </svg>
          <span>SUGAR FREE</span>
        </li>
        <li class="claim">
          <svg viewBox="0 0 74 74">
            <circle cx="37" cy="37" r="34" fill="#fff" stroke="var(--ink-soft)" stroke-width="2"/>
            <line x1="37" y1="16" x2="37" y2="60" stroke="var(--rust)" stroke-width="3"/>
            <path d="M37 24 l-8 -4 M37 24 l8 -4 M37 34 l-9 -5 M37 34 l9 -5 M37 44 l-9 -5 M37 44 l9 -5" stroke="var(--rust)" stroke-width="3" fill="none"/>
            <line x1="16" y1="16" x2="58" y2="58" stroke="var(--ink-soft)" stroke-width="2"/>
          </svg>
          <span>GLUTEN FREE</span>
        </li>
        <li class="claim">
          <svg viewBox="0 0 74 74">
            <circle cx="37" cy="37" r="34" fill="#fff" stroke="var(--ink-soft)" stroke-width="2"/>
            <path d="M37 20 L52 46 L22 46 Z" fill="none" stroke="var(--rust)" stroke-width="3" stroke-linejoin="round"/>
            <path d="M33 18 l4 2 l-2 4 M54 44 l-2 3 l-4 -1 M24 49 l-3 -3 l2 -4" stroke="var(--rust)" stroke-width="2.5" fill="none"/>
          </svg>
          <span>BIO PACKAGING</span>
        </li>
      </ul>
    </section>

    <p class="supplement">FOOD SUPPLEMENT</p>
    <p class="net-weight">NET WT 360G / 30 SERVINGS</p>
  </main>
</body>
</html>
```